Marlith Construction Core Values Wall Design

Core Values Wall Design for our Wall, I’m not exactly sure visually what we would want it to look like. Maybe some acrylic stand offs that could go on brick? If that’s a possibility. That’s where we have the most space in the office. But we could do other locations too.

These are our core values
• Safety
• Integrity
• Quality
• Client-Focused Solutions
• Continuous Improvement
• Positive Culture and Stewardship

Our vision/mission statement is Craft Assured.

```html
<!DOCTYPE html>
<html lang="en">
<head>
<meta charset="utf-8">
<title>Marlith Construction – Core Value: Quality</title>
<link rel="stylesheet" href="https://fonts.googleapis.com/css2?family=Montserrat:wght@700;900&display=swap">
<style>
  :root {
    --bg: #ebe9e7;
    --acrylic: #e4e2e3;
    --acrylic-edge: #f4f3f3;
    --brand-red: #e2363b;
    --band-dark: #1e0204;
    --brand-blue: #1a63a8;
    --white: #ffffff;
    --steel-light: #f3f3f3;
    --steel-dark: #7b7b7b;
  }
  * { box-sizing: border-box; margin: 0; padding: 0; }
  html, body { width: 1200px; height: 800px; overflow: hidden; }
  body {
    background: var(--bg);
    font-family: "Montserrat", Arial, sans-serif;
    position: relative;
  }
  .value-panel {
    position: absolute;
    left: 60px; top: 80px;
    width: 1080px; height: 640px;
    background: linear-gradient(135deg, var(--acrylic-edge), var(--acrylic));
    border: 3px solid var(--acrylic-edge);
    box-shadow: 0 10px 30px rgba(0,0,0,0.12);
  }
  .standoff {
    position: absolute;
    width: 56px; height: 56px;
    border-radius: 50%;
    background: radial-gradient(circle at 35% 35%, var(--steel-light) 0%, #c9c9c9 45%, var(--steel-dark) 100%);
  }
  .standoff.tl { left: 70px; top: 52px; }
  .standoff.tr { right: 60px; top: 52px; }
  .standoff.bl { left: 70px; bottom: 52px; }
  .standoff.br { right: 60px; bottom: 52px; }

  .value-card {
    position: absolute;
    left: 180px; top: 100px;
    width: 470px; height: 480px;
    background: var(--brand-red);
    border-radius: 12px 12px 0 0;
    overflow: hidden;
  }
  .value-icon {
    position: absolute;
    left: 75px; top: 42px;
    width: 320px; height: 320px;
  }
  .value-band {
    position: absolute;
    left: 0; bottom: 0;
    width: 100%; height: 112px;
    background: var(--band-dark);
    color: var(--white);
    font-weight: 900;
    font-size: 62px;
    letter-spacing: 1px;
    display: flex; align-items: center; justify-content: center;
  }

  .divider {
    position: absolute;
    left: 712px; top: 210px;
    width: 3px; height: 265px;
    background: var(--brand-blue);
  }
  .brand-block {
    position: absolute;
    left: 740px; top: 250px;
    width: 300px;
    text-align: center;
  }
  .brand-name {
    color: var(--brand-blue);
    font-weight: 700;
    font-size: 34px;
    line-height: 1.1;
    letter-spacing: 1px;
  }
  .brand-tagline {
    margin-top: 30px;
    color: var(--brand-red);
    font-weight: 700;
    font-size: 22px;
    letter-spacing: 3px;
    text-transform: uppercase;
  }
</style>
</head>
<body>
  <main class="value-panel">
    <span class="standoff tl"></span>
    <span class="standoff tr"></span>
    <span class="standoff bl"></span>
    <span class="standoff br"></span>

    <section class="value-card">
      <svg class="value-icon" viewBox="-200 -200 400 400" aria-hidden="true">
        <polygon fill="none" stroke="#ffffff" stroke-width="12" stroke-linejoin="round"
          points="170,0 144.9,38.9 147.2,85 106.1,106.1 85,147.2 38.9,144.9 0,170 -38.9,144.9 -85,147.2 -106.1,106.1 -147.2,85 -144.9,38.9 -170,0 -144.9,-38.9 -147.2,-85 -106.1,-106.1 -85,-147.2 -38.9,-144.9 0,-170 38.9,-144.9 85,-147.2 106.1,-106.1 147.2,-85 144.9,-38.9"/>
        <circle cx="0" cy="0" r="102" fill="none" stroke="#ffffff" stroke-width="12"/>
        <path d="M-52,2 L-14,40 L56,-32" fill="none" stroke="#ffffff" stroke-width="30" stroke-linecap="round" stroke-linejoin="round"/>
        <path d="M-52,2 L-14,40 L56,-32" fill="none" stroke="#e2363b" stroke-width="8" stroke-linecap="round" stroke-linejoin="round"/>
      </svg>
      <div class="value-band">QUALITY</div>
    </section>

    <div class="divider"></div>

    <div class="brand-block">
      <p class="brand-name">MARLITH<br>CONSTRUCTION</p>
      <p class="brand-tagline">Craft Assured</p>
    </div>
  </main>
</body>
</html>
```